Business Card for a mobile physiotherapy company

I need a layout for a business card for a mobile physiotherapy company.
Slogan is "Mobile Physiotherapy - Your Road To Recovery"
Phone number is 867-555-0142
Email VardenTherapy@postnest.ca (subject to change with website)
Website www.VardenTherapy.ca
My name and credentials: Luke Varden Luke Varden, BSc(kin), MPT, CAFCI, IMS
Information maybe included: Direct Billing, Services including Physiotherapy, IMS, acupuncture
Maybe include facebook and instagram logos
One side with the logo clean and sharp
Other side with details, try not to look too busy, keep everything concise

```html
<!DOCTYPE html>
<html lang="en">
<head>
<meta charset="utf-8">
<title>Varden Therapy – Business Card</title>
<link rel="stylesheet" href="https://fonts.googleapis.com/css2?family=Open+Sans:wght@400;600;700&display=swap">
<style>
  :root {
    --backdrop: #4a423d;
    --card: #1b1d21;
    --silver: #d9d9d9;
    --text-light: #ececec;
    --brand-blue: #3f64a3;
    --brand-green: #23745e;
    --divider: #9a9a9a;
  }
  * { margin: 0; padding: 0; box-sizing: border-box; }
  html, body {
    width: 1200px; height: 864px; overflow: hidden;
    background: var(--backdrop);
    font-family: "Open Sans", sans-serif;
  }
  .card {
    position: absolute;
    width: 540px; height: 310px;
    background: var(--card);
    border-radius: 3px;
    box-shadow: 0 14px 30px rgba(0,0,0,0.45);
  }
  .card--front { left: 60px; top: 110px; }
  .card--back  { left: 600px; top: 444px; }

  /* Front */
  .front-brand {
    position: absolute; left: 0; right: 0; top: 88px;
    display: flex; justify-content: center; align-items: center; gap: 12px;
    color: var(--silver); font-weight: 700; font-size: 34px; letter-spacing: 1px;
  }
  .front-brand .mark {
    width: 14px; height: 14px; background: var(--silver);
  }
  .front-tagline {
    position: absolute; left: 40px; bottom: 48px;
    color: var(--text-light); font-size: 14px; line-height: 1.5;
    font-style: italic;
  }
  .front-services { font-style: normal; }
  .social {
    position: absolute; right: 26px; top: 26px; display: flex; gap: 8px;
  }
  .social span {
    width: 22px; height: 22px; border-radius: 50%; background: var(--text-light);
  }

  /* Back */
  .back-brand {
    position: absolute; left: 30px; top: 0; bottom: 0; width: 210px;
    display: flex; align-items: center; justify-content: center; gap: 10px;
    color: var(--brand-blue); font-weight: 700; font-size: 24px;
  }
  .back-brand .mark { width: 12px; height: 12px; background: var(--brand-blue); }
  .divider {
    position: absolute; left: 262px; top: 60px; width: 1px; height: 190px;
    background: var(--divider);
  }
  .details {
    position: absolute; left: 288px; top: 76px; color: var(--text-light);
  }
  .details__name {
    color: var(--brand-blue); font-weight: 700; font-size: 20px; letter-spacing: 0.5px;
  }
  .details__creds { color: var(--brand-blue); font-size: 13px; margin-top: 2px; }
  .details__billing { color: var(--brand-green); font-size: 14px; font-weight: 600; margin-top: 2px; }
  .contact { list-style: none; margin-top: 16px; font-size: 14px; }
  .contact li { display: flex; align-items: center; gap: 10px; line-height: 1.65; }
  .contact svg { width: 13px; height: 13px; flex: none; fill: var(--brand-blue); }
</style>
</head>
<body>

<section class="card card--front" aria-label="Business card front">
  <div class="social" aria-label="Social media">
    <span></span><span></span>
  </div>
  <div class="front-brand"><span class="mark"></span>Varden Therapy</div>
  <p class="front-tagline">
    Mobile Physiotherapy - Your Road To Recovery<br>
    <span class="front-services">Physiotherapy • IMS • Acupuncture</span>
  </p>
</section>

<section class="card card--back" aria-label="Business card back">
  <div class="back-brand"><span class="mark"></span>Varden Therapy</div>
  <div class="divider"></div>
  <div class="details">
    <p class="details__name">LUKE VARDEN</p>
    <p class="details__creds">BSc(kin), MPT, CAFCI, IMS</p>
    <p class="details__billing">Direct Billing</p>
    <ul class="contact">
      <li>
        <svg viewBox="0 0 16 16"><path d="M3 1h3l1.5 4-2 1.3a9 9 0 0 0 4.2 4.2L11 8.5l4 1.5v3a2 2 0 0 1-2 2A12 12 0 0 1 1 3a2 2 0 0 1 2-2z"/></svg>
        867-555-0142
      </li>
      <li>
        <svg viewBox="0 0 16 16"><path d="M1 3h14v10H1z M1 3l7 6 7-6" fill="none" stroke="#3f64a3" stroke-width="1.6"/></svg>
        VardenTherapy@postnest.ca
      </li>
      <li>
        <svg viewBox="0 0 16 16"><circle cx="8" cy="8" r="6.5" fill="none" stroke="#3f64a3" stroke-width="1.6"/><path d="M1.5 8h13M8 1.5c-3 3.5-3 9.5 0 13M8 1.5c3 3.5 3 9.5 0 13" fill="none" stroke="#3f64a3" stroke-width="1.2"/></svg>
        www.VardenTherapy.ca
      </li>
    </ul>
  </div>
</section>

</body>
</html>
```